Larkfield Business Services Stationary
Letterhead, Business Card, Envelope
Larkfield Business Services Stationary -
Creative Brief
Simple
Peter Hollis
Bookkeeping and Tax Preparation
PO Box 7143 Seattle, WA 98104
phollishollis@larkfieldllc.example
www.larkfieldllc.example
The info for the business card is fake because this is not a private contest. I will provide the correct info when I finalize the contest. I need a standard sized business card, letterhead, and envelope. Finished artwork needs to be vector format. I have attached designs that I like and my company logo.
Maybe just the logo? reversed colors? I've attached samples and layouts the I like.

```html
<!DOCTYPE html>
<html lang="en">
<head>
<meta charset="utf-8">
<title>Larkfield Business Services Stationery</title>
<link href="https://fonts.googleapis.com/css2?family=Cinzel:wght@600&family=Arimo:wght@400&display=swap" rel="stylesheet">
<style>
  :root{
    --backdrop:#6b5e57;
    --paper:#ffffff;
    --band:#c9c9c9;
    --band-light:#dcdcdc;
    --ink:#2f2f2f;
    --ink-soft:#555555;
    --faint:#e6e6e6;
    --label:#ffffff;
  }
  html,body{margin:0;padding:0;overflow:hidden}
  body{width:1200px;height:871px;background:var(--backdrop);position:relative;font-family:"Arimo",Arial,sans-serif}
  .piece{position:absolute;background:var(--paper);overflow:hidden}
  .label{position:absolute;color:var(--label);font-size:22px;font-family:"Arimo",Arial,sans-serif}
  .brand{display:flex;align-items:center;gap:8px;font-family:"Cinzel",Georgia,serif;font-weight:600;color:var(--ink);letter-spacing:1px;white-space:nowrap}
  .brand .mark{display:block;background:var(--ink)}
  .contact{margin:0;font-size:9px;color:var(--ink-soft);white-space:nowrap}

  /* letterhead */
  .letterhead{left:34px;top:65px;width:520px;height:762px}
  .letterhead .stripe{position:absolute;left:0;top:0;width:53px;height:100%;background:var(--band)}
  .letterhead .brand{position:absolute;left:205px;top:50px;font-size:20px}
  .letterhead .brand .mark{width:14px;height:14px}
  .letterhead .rule{position:absolute;left:53px;right:0;top:694px;border-top:1px solid #9a9a9a}
  .letterhead .contact{position:absolute;left:70px;top:712px}

  /* business card */
  .card-front{left:572px;top:70px;width:303px;height:175px;background:var(--paper)}
  .card-front .face{position:absolute;left:0;top:0;width:235px;height:100%;background:var(--band)}
  .card-front .brand{position:absolute;left:30px;top:74px;font-size:25px}
  .card-front .brand .mark{width:18px;height:18px}
  .card-front .person{position:absolute;left:243px;top:10px;font-size:8px;color:var(--ink);line-height:1.3}
  .card-back{left:885px;top:70px;width:279px;height:175px}
  .card-back .ghost{position:absolute;left:0;right:0;top:52px;text-align:center;font-family:"Cinzel",Georgia,serif;font-weight:600;font-size:30px;color:var(--faint);letter-spacing:2px}
  .card-back .band{position:absolute;left:0;right:0;bottom:0;height:20px;background:var(--band-light)}
  .card-back .contact{position:absolute;left:0;right:0;bottom:5px;text-align:center;font-size:7px}

  /* envelope front */
  .env-front{left:601px;top:308px;width:560px;height:231px}
  .env-front .stripe{position:absolute;left:0;top:0;width:34px;height:100%;background:var(--band)}
  .env-front .brand{position:absolute;right:18px;top:178px;font-size:22px}
  .env-front .brand .mark{width:16px;height:16px}

  /* envelope back */
  .env-back{left:601px;top:592px;width:560px;height:245px}
  .env-back svg{position:absolute;left:0;top:0}
  .env-back .ghost{position:absolute;left:20px;top:110px;font-family:"Cinzel",Georgia,serif;font-weight:600;font-size:34px;color:var(--faint);letter-spacing:2px}
  .env-back .band{position:absolute;left:0;right:0;bottom:0;height:55px;background:var(--band-light)}
  .env-back .contact{position:absolute;left:150px;right:10px;bottom:22px;text-align:center;font-size:8px}
</style>
</head>
<body>
  <section class="piece letterhead">
    <div class="stripe"></div>
    <div class="brand"><span class="mark"></span>LARKFIELD</div>
    <div class="rule"></div>
    <p class="contact">PO Box 7143 Seattle, WA 98104 | Phone: (206) 555-0142 | Email: phollishollis@larkfieldllc.example</p>
  </section>

  <div class="label" style="left:660px;top:28px">FRONT</div>
  <section class="piece card-front">
    <div class="face"></div>
    <div class="brand"><span class="mark"></span>LARKFIELD</div>
    <div class="person">Bookkeeper<br>Peter Hollis</div>
  </section>

  <div class="label" style="left:985px;top:32px">BACK</div>
  <section class="piece card-back">
    <div class="ghost">LARKFIELD</div>
    <div class="band"></div>
    <p class="contact">PO Box 7143 Seattle, WA 98104 | (206) 555-0142 | phollishollis@larkfieldllc.example</p>
  </section>

  <div class="label" style="left:795px;top:275px">Envolop-Front</div>
  <section class="piece env-front">
    <div class="stripe"></div>
    <div class="brand"><span class="mark"></span>LARKFIELD</div>
  </section>

  <div class="label" style="left:803px;top:558px">Envolop-Back</div>
  <section class="piece env-back">
    <svg width="560" height="245" viewBox="0 0 560 245">
      <polyline points="0,0 280,68 560,0" fill="none" stroke="#bdbdbd" stroke-width="1.5"/>
      <polyline points="6,4 280,72 554,4" fill="none" stroke="#e2e2e2" stroke-width="1"/>
    </svg>
    <div class="ghost">LARKFIELD</div>
    <div class="band"></div>
    <p class="contact">PO Box 7143 Seattle, WA 98104 | Phone: (206) 555-0142 | Email: phollishollis@larkfieldllc.example</p>
  </section>
</body>
</html>
```